Diverse, up-scale salon needs eye-catching, unique business cards.

We are looking for a unique business card design for our stylist but that can also be multi functional and used for appointment reminder and referrals. I will need a design in a format that I can modify names and titles going forward. In the past we have had a dark background with the logo on one side, and stylist and contact information on the other but we are open to all ideas. I have included our mission statement as well as branded colors below. The statement doesn't need to go on the card, it's just a reference for target market. We need space for the stylists name, title, instagram handle and then the salons phone number, website and address. I am also open to adding a spot for a qr code linked to the stylist instagram or the salon booking link.

primary brand colors:
#333333 #233415 #36502a #93874a #000000
Mission statement:
Vessolin Hair Studio, a high-end salon located in the lively Downtown Farmington, Michigan, is committed to providing exceptional services in a welcoming and relaxed environment to meet the needs of our diverse clientele.
Our salon specializes in contemporary custom haircuts, coloring, extensions, and barbering and beard grooming services. Our team of skilled stylists is passionate and inventive in their hair styling techniques. At the heart of our salon are values centered on quality, innovation, creativity, and above all, comfort. These core values are evident in every appointment across our customizable array of services.
Our goal is to establish a benchmark for exceptional hair care for every human.
Website: www.vessolinhairstudio.example
instagram: @vessolinhairstudio
address: 41782 Pelham Crest Rd, Farmington MI
phone: 248-613-4087

Industry/Entity Type

Hair Salon

Contact Information for Business Card

Stylist name, title, phone, instagram, website, address, (optional qr code)

Requirements
Should not have
• Does not need mission statement on the card.

```html
<!DOCTYPE html>
<html lang="en">
<head>
<meta charset="utf-8">
<title>Vessolin Hair Studio – Business Card</title>
<link rel="stylesheet" href="https://fonts.googleapis.com/css2?family=Lato:wght@400;700&family=Montserrat:wght@400;700&display=swap">
<style>
  :root {
    --backdrop: #2b2d30;
    --olive: #93874a;
    --paper: #ffffff;
    --ink: #4a4a4a;
    --ink-soft: #8a8a8a;
    --white: #ffffff;
  }
  * { box-sizing: border-box; margin: 0; padding: 0; }
  html, body { width: 1200px; height: 952px; overflow: hidden; }
  body {
    background: var(--backdrop);
    font-family: "Lato", sans-serif;
    position: relative;
  }
  .card {
    position: absolute;
    width: 520px;
    height: 300px;
    border-radius: 20px;
    box-shadow: 0 3px 0 rgba(0,0,0,.12), 0 18px 40px rgba(0,0,0,.35);
    overflow: hidden;
  }
  /* Brand side */
  .card--brand {
    left: 50px;
    top: 430px;
    background: var(--olive);
    display: flex;
    align-items: center;
    justify-content: center;
    gap: 16px;
  }
  .brand-dot {
    flex: none;
    width: 22px;
    height: 22px;
    border-radius: 50%;
    border: 2px solid var(--white);
  }
  .brand-name {
    font-family: "Lato", sans-serif;
    font-weight: 700;
    font-size: 24px;
    letter-spacing: 4px;
    text-transform: uppercase;
    color: var(--white);
    white-space: nowrap;
  }
  /* Contact side */
  .card--contact {
    left: 630px;
    top: 200px;
    background: var(--paper);
    padding: 34px 36px;
  }
  .stylist-name {
    font-family: "Montserrat", sans-serif;
    font-size: 24px;
    letter-spacing: .5px;
    color: var(--olive);
    text-transform: uppercase;
    white-space: nowrap;
  }
  .stylist-name .given { font-weight: 400; }
  .stylist-name .family { font-weight: 700; }
  .stylist-title {
    margin-top: 2px;
    font-size: 14px;
    color: var(--ink);
  }
  .title-rule {
    width: 40px;
    height: 1px;
    background: var(--ink-soft);
    margin-top: 8px;
  }
  .contact-list {
    list-style: none;
    margin-top: 30px;
    display: flex;
    flex-direction: column;
    gap: 9px;
  }
  .contact-item {
    display: flex;
    align-items: flex-start;
    gap: 10px;
    font-size: 12.5px;
    line-height: 1.35;
    color: var(--ink);
    white-space: nowrap;
  }
  .contact-icon {
    flex: none;
    width: 16px;
    height: 16px;
    border-radius: 2px;
    background: var(--olive);
    display: flex;
    align-items: center;
    justify-content: center;
    margin-top: 1px;
  }
  .contact-icon svg { width: 10px; height: 10px; }
</style>
</head>
<body>

  <section class="card card--brand" aria-label="Card front">
    <span class="brand-dot" aria-hidden="true"></span>
    <span class="brand-name">Vessolin Hair Studio</span>
  </section>

  <section class="card card--contact" aria-label="Card back">
    <h1 class="stylist-name"><span class="given">Daniel R.</span> <span class="family">Whitcombe</span></h1>
    <p class="stylist-title">Managing Director</p>
    <div class="title-rule"></div>

    <ul class="contact-list">
      <li class="contact-item">
        <span class="contact-icon">
          <svg viewBox="0 0 10 10"><path d="M5 .8a3 3 0 0 0-3 3c0 2.2 3 5.4 3 5.4s3-3.2 3-5.4a3 3 0 0 0-3-3z" fill="#fff"/><circle cx="5" cy="3.8" r="1.1" fill="#93874a"/></svg>
        </span>
        <span>41782 Pelham Crest Rd<br>Farmington MI</span>
      </li>
      <li class="contact-item">
        <span class="contact-icon">
          <svg viewBox="0 0 10 10"><path d="M2.2 .9l1.6 1.9-.9 1.2a5.5 5.5 0 0 0 3.1 3.1l1.2-.9 1.9 1.6-1 1.3C4.6 8.8 1.2 5.4.9 1.9z" fill="#fff"/></svg>
        </span>
        <span>248-613-4087</span>
      </li>
      <li class="contact-item">
        <span class="contact-icon">
          <svg viewBox="0 0 10 10"><circle cx="5" cy="5" r="2" fill="#fff"/></svg>
        </span>
        <span>@vessolinhairstudio</span>
      </li>
      <li class="contact-item">
        <span class="contact-icon">
          <svg viewBox="0 0 10 10"><path d="M2.5 1l5 4.2-2.2.3 1.3 2.8-1 .5-1.3-2.8-1.8 1.4z" fill="#fff"/></svg>
        </span>
        <span>www.vessolinhairstudio.example</span>
      </li>
    </ul>
  </section>

</body>
</html>
```